Need a new updated business logo and business cards and possible car signs. Logo should be modern with bold elements. Possible use in some way of former logo may be considered. Looking for use of bold colors to grab attention with car signage/wrap in mind. Phone number should be easy to read- customers should understand what business is about- home painting, repair, renovation, 're-imagine your space' etc.

Target Market(s)

Homeowners, construction, businesses

Industry/Entity Type

Contractor

Contact Information for Business Card

Brennick Painting & Renovation, Inc.
Owner : Marcus D. Brennick
555-014-7382
marcusdbrennickmb@quillpost.net
All work is guaranteed and insured! More than 30 years of experience:
residential & commercial, Interior & Exterior, Renovation/Restoration

Logo Text

Brennick Painting & Renovation, Inc. 'Hard Working & Trustworthy'

Font styles to use
Other font styles liked:
• Designer suggestions for industry

Colors

Designer to choose colors to be used in the design.

Requirements
Must have
• New design logo-possibly incorporating old elements- new logo ok without old though as well. Cell Phone number has to be on there- Color preferable
Nice to have
• Nice to have a logo that pops and that may be used in conjunction with his parent company Brennick REAL Property, LLC.
• Business card layout of information that is clear & easy to read
Should not have
• Bulky old fonts

```html
<!DOCTYPE html>
<html lang="en">
<head>
<meta charset="utf-8">
<title>Brennick Painting &amp; Renovation – Business Card</title>
<link rel="stylesheet" href="https://fonts.googleapis.com/css2?family=Cinzel:wght@500;600&family=Lato:wght@400;700&display=swap">
<style>
  :root {
    --navy: #173a66;
    --navy-deep: #123c69;
    --slate: #808080;
    --rule: #b5b5b5;
    --ink: #1d1d1d;
    --paper: #ffffff;
    --backdrop: #2e2e2e;
  }
  * { margin: 0; padding: 0; box-sizing: border-box; }
  html, body { width: 1200px; height: 1200px; overflow: hidden; }
  body { background: var(--backdrop); position: relative; font-family: "Lato", sans-serif; }

  .card {
    position: absolute;
    top: 310px;
    height: 594px;
    box-shadow: 0 4px 10px rgba(0,0,0,.45);
    text-align: center;
  }
  .card--front { left: 234px; width: 364px; background: var(--paper); }
  .card--back  { left: 627px; width: 369px; background: var(--slate); overflow: hidden; }

  /* Front */
  .brand { position: absolute; top: 68px; left: 0; right: 0; }
  .brand__square { width: 70px; height: 70px; margin: 0 auto 18px; background: var(--navy); }
  .brand__name {
    font-family: "Cinzel", serif; font-weight: 600; color: var(--navy);
    font-size: 40px; line-height: 1; letter-spacing: .5px;
  }
  .brand__sub {
    font-family: "Cinzel", serif; font-weight: 600; color: var(--navy);
    font-size: 12.5px; letter-spacing: .4px; margin-top: 6px;
  }
  .person { position: absolute; top: 330px; left: 0; right: 0; }
  .person__name {
    font-family: "Cinzel", serif; font-weight: 500; color: var(--navy);
    font-size: 22px; letter-spacing: 1px; line-height: 1.1;
  }
  .person__role { font-size: 18px; color: var(--ink); margin-top: 2px; }
  .divider { width: 190px; height: 1px; background: var(--rule); margin: 11px auto 12px; }
  .contact { font-size: 18px; color: var(--ink); line-height: 25px; }
  .contact--email { font-size: 16.5px; }
  .address { font-size: 19px; color: var(--ink); line-height: 24px; }
  .address__company { color: var(--navy); font-weight: 700; font-size: 18.5px; }

  /* Back */
  .back__top {
    position: absolute; top: 0; left: 0; right: 0; height: 393px;
    background: var(--navy-deep);
  }
  .back__headline {
    position: absolute; top: 77px; left: 0; right: 0;
    font-family: "Cinzel", serif; font-weight: 600; color: var(--paper);
    font-size: 21px; line-height: 26px; letter-spacing: .5px;
  }
  .back__brand { position: absolute; top: 190px; left: 0; right: 0; }
  .back__square { width: 96px; height: 96px; margin: 0 auto 22px; background: var(--paper); }
  .back__name {
    font-family: "Cinzel", serif; font-weight: 600; color: var(--paper);
    font-size: 38px; line-height: 1; letter-spacing: .5px;
  }
  .back__services {
    position: absolute; top: 456px; left: 0; right: 0;
    color: var(--paper); font-size: 17px; line-height: 25px;
  }
  .back__lead { margin-bottom: 6px; }
</style>
</head>
<body>
  <section class="card card--front">
    <div class="brand">
      <div class="brand__square"></div>
      <div class="brand__name">BRENNICK'S</div>
      <div class="brand__sub">PAINTING &amp; RENOVATION, INC</div>
    </div>
    <div class="person">
      <div class="person__name">MARCUS D. BRENNICK</div>
      <div class="person__role">Owner</div>
      <div class="divider"></div>
      <div class="contact">555-014-7382</div>
      <div class="contact contact--email">marcusdbrennickmb@quillpost.net</div>
      <div class="divider"></div>
      <div class="address">
        <div class="address__company">Brennick's Painting and Renovation</div>
        <div>48 Harlow Lane</div>
        <div>Millbrook, NC 27999</div>
      </div>
    </div>
  </section>

  <section class="card card--back">
    <div class="back__top"></div>
    <div class="back__headline">ALL WORK IS GUARANTEED<br>AND INSURED!</div>
    <div class="back__brand">
      <div class="back__square"></div>
      <div class="back__name">BRENNICK'S</div>
    </div>
    <div class="back__services">
      <div class="back__lead">More than 30 years of experience.</div>
      <div>Residential &amp; commercial</div>
      <div>Interior &amp; Exterior</div>
      <div>Renovation/Restoration</div>
    </div>
  </section>
</body>
</html>
```